Template Flyer- Corewell Stretch & Flow

I am wanting a template 1 page flyer designed to use on the back ground of newsletter (faded background) and for our advertising posters in A4, A3, for Facebook and Instagram compatibility.

I have loaded an example from another Studio called Pinegrove (file 3)- each time they have a new workshop to advertise a picture is placed in the little circle (so this is something I would want to do too where I can load a new picture each time a new workshop is running)- They have used the flyer like a water mark...I like this.

Our colour palette is what is on our logos and you can also visit our website for a feel for what we like www.corewellstretch.com.au

I need some of the designs edited a bit more and because of the time difference, there seems to be a 24hour period where we communicate with each other. May I please request another 2 days extension

Requirements
Must have
• Id like to have a picture in the back ground. My favourite back ground that has been produced so far is a background of both picture file 9 and 10 in either.
Nice to have
• 3 picture circles options to advertise the events/workshops I have each year.
• Brush stroke style circles (see picture attached)rather then smooth circles for the picture area (in a grey tone)
Should not have
• No BLACK colour writing or black circles

```html
<!DOCTYPE html>
<html lang="en">
<head>
<meta charset="utf-8">
<title>Corewell Stretch &amp; Flow – Flyer</title>
<link rel="stylesheet" href="https://fonts.googleapis.com/css2?family=Mulish:wght@300;400;700&display=swap">
<style>
  :root {
    --backdrop: #3a464e;
    --paper: #ececec;
    --teal: #2a8ea8;
    --stone: #aaa39c;
    --text-grey: #808080;
    --text-dark: #444444;
    --photo-dark: #2e1f17;
    --photo-mid: #4a3326;
    --photo-skin: #b98a6a;
  }
  * { margin: 0; padding: 0; box-sizing: border-box; }
  html, body {
    width: 1200px; height: 1200px; overflow: hidden;
    background: var(--backdrop);
    font-family: "Mulish", sans-serif;
  }
  .flyer {
    position: absolute; left: 190px; top: 20px;
    width: 820px; height: 1160px;
    background: var(--paper);
    overflow: hidden;
  }
  .flyer__art { position: absolute; inset: 0; width: 100%; height: 100%; }
  .brand {
    position: absolute; top: 80px; left: 0; right: 0;
    display: flex; justify-content: center; align-items: center; gap: 18px;
  }
  .brand__dot {
    width: 70px; height: 70px; border-radius: 50%;
    border: 5px solid var(--teal);
  }
  .brand__text { display: flex; flex-direction: column; }
  .brand__name {
    font-size: 40px; font-weight: 400; color: var(--teal);
    line-height: 1.1; letter-spacing: 0.5px;
  }
  .brand__tagline {
    font-size: 14px; font-weight: 400; color: var(--teal);
    letter-spacing: 2px; margin-top: 6px; align-self: flex-end;
  }
  .headline {
    position: absolute; top: 885px; left: 0; right: 0;
    text-align: center; line-height: 1.15;
  }
  .headline__main { font-size: 39px; font-weight: 700; color: var(--teal); }
  .headline__sub { font-size: 40px; font-weight: 300; color: var(--text-grey); }
  .address {
    position: absolute; top: 1012px; left: 0; right: 0;
    text-align: center; font-size: 23px; font-weight: 400; font-style: normal;
    color: var(--text-dark); line-height: 1.3;
  }
  .website {
    position: absolute; top: 1100px; left: 0; right: 0;
    text-align: center; font-size: 16px; color: var(--teal);
    letter-spacing: 3px;
  }
</style>
</head>
<body>
  <main class="flyer">
    <svg class="flyer__art" viewBox="0 0 842 1190" preserveAspectRatio="none">
      <defs>
        <clipPath id="lower-left">
          <polygon points="0,200 160,330 760,700 842,700 842,1190 0,1190"/>
        </clipPath>
        <clipPath id="upper-right">
          <polygon points="300,0 842,0 842,720 760,700 160,330 300,200"/>
        </clipPath>
        <radialGradient id="photo-tones" cx="50%" cy="50%" r="50%">
          <stop offset="0%" stop-color="var(--photo-mid)"/>
          <stop offset="55%" stop-color="var(--photo-dark)"/>
          <stop offset="80%" stop-color="var(--photo-mid)"/>
          <stop offset="100%" stop-color="var(--photo-skin)"/>
        </radialGradient>
      </defs>
      <circle class="swoosh swoosh--stone" cx="452" cy="520" r="300" fill="var(--stone)" clip-path="url(#upper-right)"/>
      <circle class="swoosh swoosh--teal" cx="412" cy="575" r="300" fill="var(--teal)" clip-path="url(#lower-left)"/>
      <circle class="photo-gap" cx="422" cy="535" r="290" fill="var(--paper)"/>
      <circle class="workshop-photo" cx="422" cy="535" r="275" fill="url(#photo-tones)"
              role="img" aria-label="Workshop photo: a circle of outstretched arms and hands on a wooden floor, with small flowers between the fingertips"/>
    </svg>

    <header class="brand">
      <span class="brand__dot"></span>
      <div class="brand__text">
        <span class="brand__name">Corewell Stretch &amp; Flow</span>
        <span class="brand__tagline">move gently, breathe deeply</span>
      </div>
    </header>

    <section class="headline">
      <p class="headline__main">Pilates and yoga</p>
      <p class="headline__sub">for your mind, body &amp; soul</p>
    </section>

    <address class="address">
      18 Larkin St (5,531.68 mi)<br>
      Halden, Victoria 3512
    </address>

    <p class="website">www.corewellstretch.com.au</p>
  </main>
</body>
</html>
```